Mindfulness School for Children -- Business Cards

We're looking for business cards for our school directors and owners. We're a mindfulness school for children called little lanterns. Attached are our logos/icons.

```html
<!DOCTYPE html>
<html lang="en">
<head>
<meta charset="utf-8">
<title>little lanterns — Business Card</title>
<link rel="stylesheet" href="https://fonts.googleapis.com/css2?family=Raleway:wght@500&family=Arimo:wght@400&display=swap">
<style>
  :root {
    --page-bg: #ecebe8;
    --green-dark: #57a190;
    --green-light: #85c39a;
    --blue-light: #8ad6e8;
    --blue-dark: #5fb5d0;
    --frost-light: #f7f4f4;
    --frost-mid: #e4dcdc;
    --frost-edge: #d6cfd2;
    --ink-light: #ffffff;
    --brand-teal: #5aa7b4;
  }
  * { margin: 0; padding: 0; box-sizing: border-box; }
  html, body {
    width: 1200px;
    height: 900px;
    overflow: hidden;
    background: var(--page-bg);
  }
  .business-card {
    position: absolute;
    left: 100px;
    top: 140px;
    width: 1000px;
    height: 620px;
    overflow: hidden;
    background: linear-gradient(to top right, var(--green-dark), var(--green-light));
    box-shadow: 0 10px 30px rgba(0,0,0,0.12);
  }
  .card-side-band {
    position: absolute;
    left: 678px;
    top: 0;
    width: 322px;
    height: 100%;
    background: linear-gradient(to bottom, var(--blue-light), var(--blue-dark));
  }
  .brand-disc {
    position: absolute;
    left: 412px;
    top: 44px;
    width: 532px;
    height: 532px;
    border-radius: 50%;
    background: radial-gradient(circle at 45% 40%, var(--frost-light) 0%, var(--frost-mid) 65%, var(--frost-edge) 100%);
    display: flex;
    align-items: center;
    justify-content: center;
    gap: 12px;
  }
  .brand-dot {
    width: 16px;
    height: 16px;
    border-radius: 50%;
    background: var(--brand-teal);
  }
  .brand-name {
    font-family: "Raleway", sans-serif;
    font-weight: 500;
    font-size: 50px;
    color: var(--brand-teal);
    letter-spacing: 0.5px;
  }
  .contact-block {
    position: absolute;
    left: 58px;
    color: var(--ink-light);
    font-family: "Arimo", Arial, sans-serif;
  }
  .person-name {
    top: 64px;
    font-family: "Raleway", sans-serif;
    font-weight: 500;
    font-size: 43px;
    line-height: 1;
  }
  .person-title {
    top: 112px;
    font-size: 27px;
    line-height: 1;
  }
  .postal-address {
    top: 256px;
    font-size: 27px;
    line-height: 36px;
    font-style: normal;
  }
  .contact-list {
    top: 452px;
    list-style: none;
    font-size: 28px;
    line-height: 36.5px;
  }
  .contact-list li {
    display: flex;
    align-items: center;
    gap: 8px;
  }
  .contact-icon {
    width: 28px;
    height: 28px;
    flex: none;
  }
</style>
</head>
<body>
  <section class="business-card">
    <div class="card-side-band"></div>

    <div class="brand-disc">
      <span class="brand-dot"></span>
      <span class="brand-name">little lanterns</span>
    </div>

    <h1 class="contact-block person-name">Daniel Hayes</h1>
    <p class="contact-block person-title">Managing Director</p>

    <address class="contact-block postal-address">
      421, Address line<br>
      goes here<br>
      45452,Country Name
    </address>

    <ul class="contact-block contact-list">
      <li>
        <svg class="contact-icon" viewBox="0 0 24 24" aria-hidden="true">
          <path d="M6.6 10.8a15.1 15.1 0 0 0 6.6 6.6l2.2-2.2a1 1 0 0 1 1-.25 11.4 11.4 0 0 0 3.6.57 1 1 0 0 1 1 1V20a1 1 0 0 1-1 1A17 17 0 0 1 3 4a1 1 0 0 1 1-1h3.5a1 1 0 0 1 1 1c0 1.25.2 2.45.57 3.6a1 1 0 0 1-.25 1z" fill="none" stroke="#fff" stroke-width="1.8"/>
          <path d="M14 3a7 7 0 0 1 7 7M14 6.5a3.5 3.5 0 0 1 3.5 3.5" fill="none" stroke="#fff" stroke-width="1.8"/>
        </svg>
        044-987 654 321
      </li>
      <li>
        <svg class="contact-icon" viewBox="0 0 24 24" aria-hidden="true">
          <rect x="2" y="5" width="20" height="14" fill="#fff"/>
          <path d="M2 5l10 8 10-8M2 19l7.5-7M22 19l-7.5-7" fill="none" stroke="#6db39c" stroke-width="1.5"/>
        </svg>
        hello@littlelanterns.org
      </li>
      <li>
        <svg class="contact-icon" viewBox="0 0 24 24" aria-hidden="true">
          <g fill="none" stroke="#fff" stroke-width="1.6">
            <circle cx="12" cy="12" r="10"/>
            <ellipse cx="12" cy="12" rx="4.5" ry="10"/>
            <path d="M2 12h20M4 7h16M4 17h16"/>
          </g>
        </svg>
        www.littlelanterns.org
      </li>
    </ul>
  </section>
</body>
</html>
```